Small Business coaching and services company

Need a powerpoint template design for a company that provides Human Resources services as well sales and business coaching.

```html
<!DOCTYPE html>
<html lang="en">
<head>
<meta charset="utf-8">
<title>CoachWorks – Presentation Template Overview</title>
<link href="https://fonts.googleapis.com/css2?family=Roboto:wght@300;400;500;700&display=swap" rel="stylesheet">
<style>
:root{
  --purple:#5b3a8e;
  --orange:#f5a623;
  --teal:#14a39a;
  --pink:#f05a78;
  --cream:#efe6b4;
  --grey:#e2e2e2;
  --ink:#555;
  --bg:#ffffff;
}
*{box-sizing:border-box;margin:0;padding:0}
html,body{width:1200px;height:1200px;overflow:hidden;background:var(--bg);font-family:"Roboto",sans-serif;color:var(--ink)}
.canvas{position:relative;width:1200px;height:1200px}
.slide{position:absolute;width:260px;height:146px;background:#fff;overflow:hidden;box-shadow:0 3px 10px rgba(0,0,0,.22)}
.c1{left:50px}.c2{left:331px}.c3{left:614px}.c4{left:896px}
.r1{top:65px}.r2{top:252px}.r3{top:439px}.r4{top:626px}.r5{top:812px}.r6{top:999px}
.abs{position:absolute}
.logo{position:absolute;display:flex;align-items:center;gap:2px;font-size:5.5px;font-weight:700;color:var(--purple)}
.logo i{display:block;width:6px;height:6px;border-radius:50%;background:var(--orange)}
.logo.lg{font-size:8.5px}.logo.lg i{width:9px;height:9px}
.title{position:absolute;color:var(--purple);font-weight:400;font-size:8.5px;line-height:1.1;text-transform:uppercase;letter-spacing:.1px}
.title b{font-weight:500}
.sub{position:absolute;color:var(--purple);font-size:5px;text-transform:uppercase;opacity:.85}
.p{position:absolute;font-size:2.6px;line-height:1.45;color:#666;text-align:justify}
.ph{position:absolute}
.ph-office{background:linear-gradient(135deg,#6b4a36,#b58a66 45%,#e0c9a8)}
.ph-desk{background:linear-gradient(135deg,#f1f1f1,#cfcfcf 60%,#8c8c8c)}
.ph-crowd{background:linear-gradient(160deg,#d8d8d8,#7a7a7a 50%,#2f2f2f)}
.ph-dark{background:linear-gradient(135deg,#2d2d36,#575763 60%,#9a9aa5)}
.ph-man{background:linear-gradient(135deg,#e8e8e8,#8a7f78 55%,#3a3535)}
.ph-stairs{background:linear-gradient(180deg,#c9d3de,#5a6c80 60%,#1f2a38)}
.ph-line{background:linear-gradient(160deg,#ffffff,#f1eef6 55%,#e9e4f1)}
.foot{position:absolute;left:0;right:0;bottom:0;height:5px;background:var(--purple);display:flex;align-items:center;justify-content:space-between;padding:0 20px;font-size:2.4px;color:#fff}
.foot::after{content:"";position:absolute;right:0;top:0;bottom:0;width:20%;background:var(--orange);z-index:0}
.foot span{position:relative;z-index:1}
.foot.plain{background:none;color:var(--purple)}
.foot.plain::after{display:none}
.dot{position:absolute;border-radius:50%}
.lbl{position:absolute;font-size:3.4px;color:var(--purple);font-weight:500;text-transform:uppercase}
.ctr{text-align:center}
</style>
</head>
<body>
<div class="canvas">

<!-- 1 cover -->
<section class="slide c1 r1">
  <div class="ph ph-desk" style="left:0;top:0;width:260px;height:146px" role="img" aria-label="Person typing on a laptop at a white desk"></div>
  <div class="abs" style="left:0;top:0;width:120px;height:146px;background:linear-gradient(90deg,rgba(255,255,255,.9),rgba(255,255,255,0))"></div>
  <div class="logo lg" style="left:18px;top:53px"><i></i>CoachWorks</div>
  <div class="title" style="left:20px;top:74px;font-size:10.5px;line-height:1.25">Your title<br>presentation<br>goes here</div>
</section>

<!-- 2 title band -->
<section class="slide c2 r1">
  <div class="ph ph-dark" style="left:0;top:0;width:69px;height:56px" role="img" aria-label="Team meeting around a table"></div>
  <div class="ph ph-office" style="left:71px;top:0;width:71px;height:56px" role="img" aria-label="Colleagues reviewing documents"></div>
  <div class="ph ph-office" style="left:144px;top:0;width:116px;height:56px" role="img" aria-label="Workshop in a bright office"></div>
  <div class="logo lg" style="left:18px;top:66px"><i></i>CoachWorks</div>
  <div class="title" style="left:101px;top:68px;font-size:10px">Your title <b>presentation</b></div>
  <div class="ph ph-dark" style="left:0;top:90px;width:189px;height:56px" role="img" aria-label="Card terminal and laptop on a desk"></div>
  <div class="ph ph-crowd" style="left:191px;top:90px;width:69px;height:56px" role="img" aria-label="Commuters walking in a busy hall"></div>
  <div class="foot plain" style="color:#fff"><span>Human Resources services &amp; business coaching</span></div>
</section>

<!-- 3 agenda -->
<section class="slide c3 r1">
  <div class="ph ph-desk" style="left:0;top:0;width:89px;height:146px" role="img" aria-label="Hands filling in a form on a clipboard"></div>
  <div class="title" style="left:197px;top:17px;font-size:10px">Agenda</div>
  <div class="abs" style="left:116px;top:32px;font-size:4px;line-height:9.7px;color:#555">
    <div><span style="color:var(--purple);display:inline-block;width:13px">01</span>Open slide</div>
    <div><span style="color:var(--purple);display:inline-block;width:13px">02</span>Agenda slide</div>
    <div><span style="color:var(--purple);display:inline-block;width:13px">03</span>Different main chapter slides</div>
    <div><span style="color:var(--purple);display:inline-block;width:13px">04</span>About us</div>
    <div><span style="color:var(--purple);display:inline-block;width:13px">05</span>Products</div>
    <div><span style="color:var(--purple);display:inline-block;width:13px">06</span>Applications</div>
    <div><span style="color:var(--purple);display:inline-block;width:13px">07</span>Technical specifications</div>
    <div><span style="color:var(--purple);display:inline-block;width:13px">08</span>Testing and benchmark</div>
    <div><span style="color:var(--purple);display:inline-block;width:13px">09</span>Q&amp;A slide</div>
    <div><span style="color:var(--purple);display:inline-block;width:13px">10</span>Conclusion slide</div>
  </div>
  <div class="foot plain"><span>Human Resources services &amp; business coaching</span><span>CoachWorks 3</span></div>
</section>

<!-- 4 about us -->
<section class="slide c4 r1">
  <div class="logo" style="left:18px;top:8px"><i></i>CoachWorks</div>
  <div class="title" style="left:104px;top:20px;font-size:10px"><b>About us</b></div>
  <div class="p ctr" style="left:22px;top:39px;width:216px">We help small firms build strong teams, hire well and grow sales. Our coaches work side by side with owners to set clear goals, shape daily habits and keep the business moving. Since day one we have kept our promise simple: practical advice, honest feedback and results you can measure in the numbers every month.</div>
  <div class="ph ph-dark" style="left:0;top:70px;width:85px;height:64px" role="img" aria-label="Business meeting, dark tone"></div>
  <div class="ph ph-office" style="left:87px;top:70px;width:86px;height:64px;filter:brightness(.55)" role="img" aria-label="Office workshop, warm tone"></div>
  <div class="ph" style="left:175px;top:70px;width:85px;height:64px;background:linear-gradient(135deg,#1b8f87,#3fb7a8)" role="img" aria-label="Team collaboration, teal tone"></div>
  <div class="lbl ctr" style="left:0;top:79px;width:85px;color:#fff;font-weight:400">Reliable alternative</div>
  <div class="lbl ctr" style="left:87px;top:79px;width:86px;color:#fff;font-weight:400">Smart services</div>
  <div class="lbl ctr" style="left:175px;top:79px;width:85px;color:#fff;font-weight:400">Trustable experience</div>
  <div class="p" style="left:10px;top:89px;width:65px;color:#fff">Clear plans for hiring, onboarding and payroll so owners can focus on their customers every day.</div>
  <div class="p" style="left:97px;top:89px;width:66px;color:#fff">Sales coaching that turns first calls into lasting deals with simple, proven steps each week.</div>
  <div class="p" style="left:185px;top:89px;width:65px;color:#fff">Years of hands-on work with growing firms across many trades and service markets today.</div>
  <div class="foot"><span>Human Resources services &amp; business coaching</span><span>CoachWorks 4</span></div>
</section>

<!-- 5 -->
<section class="slide c1 r2">
  <div class="logo" style="left:18px;top:8px"><i></i>CoachWorks</div>
  <div class="title" style="left:19px;top:23px;font-size:9.5px">Your title <b>slide goes here</b></div>
  <div class="sub" style="left:19px;top:39px;font-size:3.6px">Your sub title slide goes here</div>
  <div class="p" style="left:19px;top:46px;width:222px">Good coaching starts with listening. We sit with your team, learn how work really flows and find the small changes that make the biggest gains. From job roles to review cycles and sales targets, every plan is built around your people and your goals so progress lasts.</div>
  <div class="ph ph-office" style="left:0;top:73px;width:260px;height:73px" role="img" aria-label="Team working on laptops around a meeting table"></div>
  <div class="foot plain" style="color:#fff"><span>Human Resources services &amp; business coaching</span></div>
</section>

<!-- 6 -->
<section class="slide c2 r2">
  <div class="logo" style="left:18px;top:8px"><i></i>CoachWorks</div>
  <div class="title" style="left:19px;top:43px;font-size:10px;line-height:1.3">Your title<br><b>slide goes here</b></div>
  <div class="sub" style="left:19px;top:71px">Sub title</div>
  <div class="p" style="left:19px;top:81px;width:97px">Our sessions follow a clear path: review where you are, agree where you want to be and map the steps between. Each coach brings real field experience in people matters and selling, and stays with you until the new habits hold. Short check-ins keep everyone on track.</div>
  <div class="ph ph-man" style="left:130px;top:0;width:130px;height:146px" role="img" aria-label="Businessman writing beside an hourglass and laptop"></div>
  <div class="foot plain"><span>Human Resources services &amp; business coaching</span></div>
</section>

<!-- 7 -->
<section class="slide c3 r2">
  <div class="logo" style="left:18px;top:8px"><i></i>CoachWorks</div>
  <div class="title ctr" style="left:0;top:27px;width:260px;font-size:8.5px">Your title <b>slide goes here</b></div>
  <div class="ph ph-crowd" style="left:0;top:41px;width:160px;height:48px" role="img" aria-label="People walking through a city hall"></div>
  <div class="ph ph-crowd" style="left:160px;top:41px;width:100px;height:48px;opacity:.8" role="img" aria-label="Commuters on a station floor"></div>
  <div class="dot" style="left:19px;top:94px;width:14px;height:14px;background:var(--orange)"></div>
  <div class="dot" style="left:137px;top:94px;width:14px;height:14px;background:var(--orange)"></div>
  <div class="lbl" style="left:41px;top:94px;font-weight:400">Subtitle slide</div>
  <div class="lbl" style="left:159px;top:94px;font-weight:400">Subtitle slide</div>
  <div class="p" style="left:41px;top:99px;width:80px">Short note that explains this point in one or two clear lines.</div>
  <div class="p" style="left:159px;top:99px;width:80px">Short note that explains this point in one or two clear lines.</div>
  <div class="p ctr" style="left:26px;top:114px;width:210px">Every service is shaped around your business size, budget and goals, with plain reports that show what changed and what comes next for your team and your sales.</div>
  <div class="foot"><span>Human Resources services &amp; business coaching</span><span>CoachWorks 7</span></div>
</section>

<!-- 8 -->
<section class="slide c4 r2">
  <div class="logo" style="left:18px;top:8px"><i></i>CoachWorks</div>
  <div class="title" style="left:69px;top:27px">Your title <b>slide goes here</b></div>
  <div class="ph ph-desk" style="left:0;top:42px;width:145px;height:53px" role="img" aria-label="Hands reviewing a document on a clipboard"></div>
  <div class="dot" style="left:159px;top:44px;width:15px;height:15px;background:var(--purple)"></div>
  <div class="dot" style="left:159px;top:63px;width:15px;height:15px;background:var(--orange)"></div>
  <div class="dot" style="left:159px;top:82px;width:15px;height:15px;background:var(--teal)"></div>
  <div class="p" style="left:182px;top:45px;width:66px">Plan roles and hiring steps with a clear, simple checklist.</div>
  <div class="p" style="left:182px;top:64px;width:66px">Train managers to give feedback that people act upon.</div>
  <div class="p" style="left:182px;top:83px;width:66px">Track sales targets with weekly coaching and reviews.</div>
  <div class="sub" style="left:20px;top:104px;font-size:3.6px">Subtitle</div>
  <div class="p" style="left:20px;top:110px;width:222px">Each step is agreed with you before it starts. We set a clear budget, a short timeline and the measures that matter, then share honest updates so you always know how the work is going and where it will lead next.</div>
  <div class="foot"><span>Human Resources services &amp; business coaching</span><span>CoachWorks 8</span></div>
</section>

<!-- 9 -->
<section class="slide c1 r3">
  <div class="logo" style="left:18px;top:8px"><i></i>CoachWorks</div>
  <div class="title" style="left:70px;top:27px">Your title <b>slide goes here</b></div>
  <div class="dot" style="left:17px;top:45px;width:15px;height:15px;background:var(--purple)"></div>
  <div class="dot" style="left:17px;top:63px;width:15px;height:15px;background:var(--teal)"></div>
  <div class="dot" style="left:17px;top:81px;width:15px;height:15px;background:var(--orange)"></div>
  <div class="p" style="left:41px;top:45px;width:60px">Time plans that keep each project on schedule.</div>
  <div class="p" style="left:41px;top:63px;width:60px">Fresh ideas for teams that need a new direction.</div>
  <div class="p" style="left:41px;top:81px;width:60px">Rewards that keep top staff proud and loyal.</div>
  <div class="ph ph-desk" style="left:114px;top:42px;width:146px;height:53px" role="img" aria-label="Colleagues discussing notes at a desk"></div>
  <div class="sub" style="left:19px;top:104px;font-size:3.6px">Subtitle</div>
  <div class="p" style="left:19px;top:110px;width:222px">Each step is agreed with you before it starts. We set a clear budget, a short timeline and the measures that matter, then share honest updates so you always know how the work is going and where it will lead next.</div>
  <div class="foot"><span>Human Resources services &amp; business coaching</span><span>CoachWorks 9</span></div>
</section>

<!-- 10 -->
<section class="slide c2 r3">
  <div class="ph ph-desk" style="left:0;top:0;width:130px;height:146px" role="img" aria-label="Laptop, coffee cup and phone on a white desk"></div>
  <div class="logo" style="left:197px;top:8px"><i></i>CoachWorks</div>
  <div class="title" style="left:147px;top:41px;font-size:8.5px;line-height:1.3">Your title<br><b>slide goes here</b></div>
  <div class="sub" style="left:147px;top:68px">Sub title</div>
  <div class="p" style="left:147px;top:79px;width:96px">Our sessions follow a clear path: review where you are, agree where you want to be and map the steps between. Each coach brings real field experience and stays with you until new habits hold.</div>
  <div class="foot plain"><span></span><span>CoachWorks 10</span></div>
</section>

<!-- 11 -->
<section class="slide c3 r3">
  <div class="logo" style="left:18px;top:8px"><i></i>CoachWorks</div>
  <div class="title" style="left:19px;top:43px;font-size:8.5px;line-height:1.3">Your title<br><b>slide goes here</b></div>
  <div class="sub" style="left:19px;top:71px">Sub title</div>
  <div class="p" style="left:19px;top:82px;width:80px">Our sessions follow a clear path: review where you are, agree where you want to be and map the steps between. Each coach brings real field experience and stays with you until new habits hold firm.</div>
  <div class="ph ph-crowd" style="left:115px;top:0;width:45px;height:94px" role="img" aria-label="Crowd seen from above"></div>
  <div class="ph ph-desk" style="left:162px;top:0;width:98px;height:94px" role="img" aria-label="Hand writing on a clipboard"></div>
  <div class="ph ph-office" style="left:115px;top:96px;width:88px;height:50px" role="img" aria-label="Team at a meeting table"></div>
  <div class="ph ph-office" style="left:205px;top:96px;width:55px;height:50px;opacity:.8" role="img" aria-label="Colleague working on a laptop"></div>
  <div class="foot plain"><span>Human Resources services &amp; business coaching</span><span></span></div>
</section>

<!-- 12 -->
<section class="slide c4 r3">
  <div class="ph ph-crowd" style="left:0;top:0;width:45px;height:94px" role="img" aria-label="Crowd seen from above"></div>
  <div class="ph ph-desk" style="left:47px;top:0;width:98px;height:94px" role="img" aria-label="Laptop and coffee on a desk"></div>
  <div class="ph ph-office" style="left:0;top:96px;width:88px;height:50px" role="img" aria-label="Team at a meeting table"></div>
  <div class="ph ph-office" style="left:90px;top:96px;width:55px;height:50px;opacity:.8" role="img" aria-label="Colleague working on a laptop"></div>
  <div class="logo" style="left:197px;top:8px"><i></i>CoachWorks</div>
  <div class="title" style="left:160px;top:41px;font-size:8.5px;line-height:1.3">Your title<br><b>slide goes here</b></div>
  <div class="sub" style="left:160px;top:68px">Sub title</div>
  <div class="p" style="left:160px;top:79px;width:84px">Our sessions follow a clear path: review where you are, agree where you want to be and map the steps between. Each coach brings real field experience and stays with you until new habits hold firm.</div>
  <div class="foot plain"><span></span><span>CoachWorks 12</span></div>
</section>

<!-- 13 -->
<section class="slide c1 r4">
  <div class="logo" style="left:18px;top:8px"><i></i>CoachWorks</div>
  <div class="title" style="left:70px;top:27px">Your title <b>slide goes here</b></div>
  <div class="lbl" style="left:7px;top:41px;font-weight:400">Service 1</div>
  <div class="lbl" style="left:131px;top:41px;font-weight:400">Service 2</div>
  <div class="p" style="left:7px;top:46px;width:118px">Hiring support from job post to first day, with contracts, handbooks and payroll set up the right way for a small team.</div>
  <div class="p" style="left:131px;top:46px;width:118px">Sales coaching for owners and reps, with call plans, follow-up habits and weekly reviews that lift closing rates.</div>
  <div class="ph ph-office" style="left:0;top:73px;width:128px;height:73px" role="img" aria-label="Team working around a table"></div>
  <div class="ph ph-desk" style="left:131px;top:73px;width:129px;height:73px" role="img" aria-label="Person writing on a clipboard"></div>
  <div class="foot plain" style="color:#fff"><span>Human Resources services &amp; business coaching</span><span>CoachWorks 13</span></div>
</section>

<!-- 14 -->
<section class="slide c2 r4">
  <div class="logo" style="left:18px;top:8px"><i></i>CoachWorks</div>
  <div class="title" style="left:70px;top:27px">Your title <b>slide goes here</b></div>
  <div class="lbl" style="left:7px;top:41px;font-weight:400">Service 1</div>
  <div class="lbl" style="left:89px;top:41px;font-weight:400">Service 2</div>
  <div class="lbl" style="left:176px;top:41px;font-weight:400">Service 3</div>
  <div class="p" style="left:7px;top:46px;width:76px">Hiring help from the first post to day one.</div>
  <div class="p" style="left:89px;top:46px;width:76px">Coaching for owners who lead growing teams.</div>
  <div class="p" style="left:176px;top:46px;width:76px">Sales plans with weekly check-ins and goals.</div>
  <div class="ph ph-office" style="left:0;top:64px;width:85px;height:82px" role="img" aria-label="Woman working on a laptop"></div>
  <div class="ph ph-man" style="left:87px;top:64px;width:86px;height:82px" role="img" aria-label="Businessman with an hourglass"></div>
  <div class="ph ph-stairs" style="left:175px;top:64px;width:85px;height:82px" role="img" aria-label="Person climbing city stairs"></div>
  <div class="foot plain" style="color:#fff"><span>Human Resources services &amp; business coaching</span><span>CoachWorks 14</span></div>
</section>

<!-- 15 -->
<section class="slide c3 r4">
  <div class="logo" style="left:18px;top:8px"><i></i>CoachWorks</div>
  <div class="title ctr" style="left:0;top:22px;width:260px">Your title <b>slide goes here</b></div>
  <div class="ph ph-desk" style="left:0;top:41px;width:94px;height:63px" role="img" aria-label="Colleagues reviewing paperwork"></div>
  <div class="abs ctr" style="left:94px;top:41px;width:73px;height:63px;background:var(--orange);color:#fff;padding:15px 7px 0">
    <div style="font-size:4px;font-weight:700;margin-bottom:2px">LOREM IPSUM</div>
    <div style="font-size:3px;line-height:1.4">A short highlight that sums up the key benefit in a few words.</div>
  </div>
  <div class="ph ph-man" style="left:167px;top:41px;width:93px;height:63px" role="img" aria-label="Businessman writing next to an hourglass"></div>
  <div class="sub" style="left:17px;top:109px;font-size:3.4px">Product description</div>
  <div class="p" style="left:17px;top:114px;width:226px">Each program is built for small firms that want stronger teams and steadier sales. Pick a single service or combine people support with coaching, and we will shape the plan around your size, your budget and the goals you set for the year ahead.</div>
  <div class="foot"><span>Human Resources services &amp; business coaching</span><span>CoachWorks 15</span></div>
</section>

<!-- 16 gallery -->
<section class="slide c4 r4">
  <div class="title" style="left:20px;top:11px;font-size:8.5px">Gallery <b>services slide</b></div>
  <div class="p" style="left:20px;top:26px;width:222px">A quick look at the services we offer to owners, managers and sales teams, with a short note on what each one covers and who it suits best.</div>
  <div class="ph ph-office" style="left:7px;top:42px;width:70px;height:43px" role="img" aria-label="Workshop with a presenter"></div>
  <div class="ph ph-desk" style="left:7px;top:91px;width:70px;height:42px" role="img" aria-label="Person reviewing a document"></div>
  <div class="abs" style="left:101px;top:47px;font-size:4px;font-weight:500;color:var(--purple)">Product 1</div>
  <div class="p" style="left:101px;top:53px;width:140px">Team health check with staff surveys, role reviews and a clear action plan. We look at turnover, training needs and pay so you know where to invest first and what can wait for later in the year.</div>
  <div class="abs" style="left:101px;top:97px;font-size:4px;font-weight:500;color:var(--purple)">Product 2</div>
  <div class="p" style="left:101px;top:103px;width:140px">Sales growth program with pipeline setup, call scripts and weekly coaching for each rep. Progress is tracked in simple reports so the owner sees every win and every gap as it happens.</div>
  <div class="foot"><span>Human Resources services &amp; business coaching</span><span>CoachWorks 16</span></div>
</section>

<!-- 17 circles -->
<section class="slide c1 r5">
  <div class="logo" style="left:18px;top:8px"><i></i>CoachWorks</div>
  <div class="title" style="left:82px;top:8px">Your title <b>slide here</b></div>
  <svg class="abs" style="left:0;top:30px" width="260" height="111" viewBox="0 0 260 111">
    <circle cx="48" cy="55" r="42" fill="var(--grey)"/>
    <circle cx="103" cy="55" r="42" fill="var(--grey)"/>
    <circle cx="157" cy="55" r="42" fill="var(--grey)"/>
    <circle cx="212" cy="55" r="42" fill="var(--cream)"/>
    <path d="M6 55 A42 42 0 0 1 90 55 Z" fill="var(--orange)"/>
    <path d="M61 55 A42 42 0 0 0 145 55 Z" fill="var(--pink)"/>
    <path d="M115 55 A42 42 0 0 1 199 55 Z" fill="var(--teal)"/>
    <path d="M170 55 A42 42 0 0 1 254 55 Z" fill="var(--grey)"/>
    <g font-family="Roboto,sans-serif" font-size="10" fill="var(--purple)" text-anchor="middle">
      <circle cx="48" cy="55" r="9" fill="#fff" stroke="var(--purple)" stroke-width="1.5"/><text x="48" y="59">1</text>
      <circle cx="103" cy="55" r="9" fill="#fff" stroke="var(--purple)" stroke-width="1.5"/><text x="103" y="59">2</text>
      <circle cx="157" cy="55" r="9" fill="#fff" stroke="var(--purple)" stroke-width="1.5"/><text x="157" y="59">3</text>
      <circle cx="212" cy="55" r="9" fill="#fff" stroke="var(--purple)" stroke-width="1.5"/><text x="212" y="59">4</text>
    </g>
    <g font-family="Roboto,sans-serif" font-size="3.4" fill="#fff" text-anchor="middle">
      <text x="48" y="29">Review where the</text><text x="48" y="33">business stands</text>
      <text x="103" y="79">Set clear goals</text><text x="103" y="83">for the team</text>
      <text x="157" y="29">Coach each step</text><text x="157" y="33">week by week</text>
      <text x="212" y="79">Measure results</text><text x="212" y="83">and adjust</text>
    </g>
  </svg>
  <div class="foot"><span>Human Resources services &amp; business coaching</span><span>CoachWorks 17</span></div>
</section>

<!-- 18 percentages -->
<section class="slide c2 r5">
  <div class="logo" style="left:18px;top:8px"><i></i>CoachWorks</div>
  <div class="title" style="left:82px;top:8px">Your title <b>slide here</b></div>
  <svg class="abs" style="left:0;top:38px" width="260" height="50" viewBox="0 0 260 50">
    <g fill="none" stroke-width="1.3" stroke-linecap="round">
      <circle cx="42" cy="24" r="22" stroke="#ececec"/><circle cx="99" cy="24" r="22" stroke="#ececec"/><circle cx="159" cy="24" r="22" stroke="#ececec"/><circle cx="216" cy="24" r="22" stroke="#ececec"/>
      <circle cx="42" cy="24" r="22" stroke="var(--orange)" stroke-dasharray="94 138" transform="rotate(-90 42 24)"/>
      <circle cx="99" cy="24" r="22" stroke="var(--orange)" stroke-dasharray="59 138" transform="rotate(-90 99 24)"/>
      <circle cx="159" cy="24" r="22" stroke="var(--orange)" stroke-dasharray="69 138" transform="rotate(-90 159 24)"/>
      <circle cx="216" cy="24" r="22" stroke="var(--orange)" stroke-dasharray="112 138" transform="rotate(-90 216 24)"/>
    </g>
    <g font-family="Roboto,sans-serif" font-size="8" fill="#555" text-anchor="middle">
      <text x="42" y="27">68%</text><text x="99" y="27">43%</text><text x="159" y="27">50%</text><text x="216" y="27">81%</text>
    </g>
  </svg>
  <div class="lbl" style="left:21px;top:98px">Título</div>
  <div class="p" style="left:21px;top:105px;width:220px">These figures show the share of client firms that improved staff retention, sales, manager confidence and overall growth within the first year of working with our coaches and people team.</div>
  <div class="foot"><span>Human Resources services &amp; business coaching</span><span>CoachWorks 18</span></div>
</section>

<!-- 19 cycle icons -->
<section class="slide c3 r5">
  <div class="logo" style="left:18px;top:8px"><i></i>CoachWorks</div>
  <div class="title" style="left:82px;top:8px">Your title <b>slide here</b></div>
  <div class="lbl" style="left:20px;top:40px">Título</div>
  <div class="p" style="left:20px;top:46px;width:76px;text-align:left">A four step loop: plan the work, build the tools, train the team and review what was sold each month.</div>
  <svg class="abs" style="left:100px;top:22px" width="160" height="85" viewBox="0 0 160 85">
    <g fill="none" stroke="#ccc" stroke-width="1">
      <path d="M40 20 H80"/><path d="M100 66 H60"/>
      <path d="M100 20 H115 V60" /><path d="M30 66 H15 V25 H30"/>
    </g>
    <circle cx="30" cy="21" r="15" fill="var(--purple)"/>
    <circle cx="89" cy="21" r="15" fill="var(--orange)"/>
    <circle cx="19" cy="65" r="15" fill="var(--teal)"/>
    <circle cx="92" cy="65" r="15" fill="var(--pink)"/>
    <g fill="none" stroke="#fff" stroke-width="1">
      <rect x="24" y="16" width="11" height="10" rx="1"/>
      <path d="M84 26 L94 16"/><path d="M86 26 L96 18"/>
      <path d="M13 62 H25 L23 70 H15 Z"/>
      <path d="M88 59 V72 M88 60 H97 L95 63 L97 66 H88"/>
    </g>
  </svg>
  <div class="p" style="left:20px;top:110px;width:222px;text-align:left">The loop repeats every quarter so the plan stays fresh and the team keeps learning. Each round ends with a short report that shows what worked, what to drop and where to focus next.</div>
  <div class="foot"><span>Human Resources services &amp; business coaching</span><span>CoachWorks 19</span></div>
</section>

<!-- 20 pins -->
<section class="slide c4 r5">
  <div class="logo" style="left:18px;top:8px"><i></i>CoachWorks</div>
  <div class="title" style="left:82px;top:8px">Your title <b>slide here</b></div>
  <svg class="abs" style="left:0;top:30px" width="260" height="70" viewBox="0 0 260 70">
    <g stroke-width="1">
      <line x1="39" y1="22" x2="39" y2="57" stroke="var(--teal)"/><circle cx="39" cy="57" r="1.5" fill="var(--teal)"/><circle cx="39" cy="22" r="17" fill="var(--teal)"/>
      <line x1="100" y1="22" x2="100" y2="57" stroke="var(--orange)"/><circle cx="100" cy="57" r="1.5" fill="var(--orange)"/><circle cx="100" cy="22" r="17" fill="var(--orange)"/>
      <line x1="161" y1="22" x2="161" y2="57" stroke="var(--pink)"/><circle cx="161" cy="57" r="1.5" fill="var(--pink)"/><circle cx="161" cy="22" r="17" fill="var(--pink)"/>
      <line x1="222" y1="22" x2="222" y2="57" stroke="var(--cream)"/><circle cx="222" cy="22" r="17" fill="var(--cream)"/>
    </g>
    <g fill="none" stroke="#fff" stroke-width="1">
      <circle cx="42" cy="19" r="4"/><path d="M39 22 L33 28 M35 26 L37 28"/>
      <path d="M94 15 H106 V29 L100 24 L94 29 Z"/>
      <path d="M161 14 L168 17 V22 C168 26 161 30 161 30 C161 30 154 26 154 22 V17 Z"/>
      <path d="M215 27 L229 17 M218 24 L222 30"/>
    </g>
  </svg>
  <div class="lbl ctr" style="left:9px;top:99px;width:60px">Título 1</div>
  <div class="lbl ctr" style="left:70px;top:99px;width:60px">Título 2</div>
  <div class="lbl ctr" style="left:131px;top:99px;width:60px">Título 3</div>
  <div class="lbl ctr" style="left:192px;top:99px;width:60px">Título 4</div>
  <div class="p ctr" style="left:11px;top:105px;width:56px">Keys to hiring the right people for your team.</div>
  <div class="p ctr" style="left:72px;top:105px;width:56px">Saved plans ready for every new starter.</div>
  <div class="p ctr" style="left:133px;top:105px;width:56px">Safe, fair policies that protect the firm.</div>
  <div class="p ctr" style="left:194px;top:105px;width:56px">A clear view of where sales can grow.</div>
  <div class="foot"><span>Human Resources services &amp; business coaching</span><span>CoachWorks 20</span></div>
</section>

<!-- 21 icon grid -->
<section class="slide c1 r6">
  <div class="logo" style="left:18px;top:8px"><i></i>CoachWorks</div>
  <div class="title" style="left:82px;top:8px">Your title <b>slide here</b></div>
  <svg class="abs" style="left:0;top:22px" width="260" height="95" viewBox="0 0 260 95">
    <circle cx="36" cy="16" r="11" fill="var(--orange)"/><circle cx="102" cy="16" r="11" fill="var(--pink)"/><circle cx="165" cy="16" r="11" fill="var(--teal)"/><circle cx="222" cy="16" r="11" fill="var(--cream)"/>
    <circle cx="36" cy="67" r="11" fill="var(--cream)"/><circle cx="102" cy="67" r="11" fill="var(--teal)"/><circle cx="165" cy="67" r="11" fill="var(--pink)"/><circle cx="222" cy="67" r="11" fill="var(--orange)"/>
    <g fill="none" stroke="#fff" stroke-width=".8">
      <rect x="31" y="13" width="10" height="7"/><rect x="97" y="12" width="10" height="8"/><rect x="160" y="12" width="10" height="8"/><rect x="217" y="12" width="10" height="8"/>
      <path d="M31 72 L41 62"/><rect x="97" y="63" width="10" height="8"/><rect x="160" y="63" width="10" height="8"/><rect x="217" y="63" width="10" height="8"/>
    </g>
  </svg>
  <div class="lbl ctr" style="left:6px;top:54px;width:60px">Título</div>
  <div class="lbl ctr" style="left:72px;top:54px;width:60px">Título</div>
  <div class="lbl ctr" style="left:135px;top:54px;width:60px">Título</div>
  <div class="lbl ctr" style="left:192px;top:54px;width:60px">Título</div>
  <div class="p ctr" style="left:6px;top:60px;width:60px">Short line about this service</div>
  <div class="p ctr" style="left:72px;top:60px;width:60px">Short line about this service</div>
  <div class="p ctr" style="left:135px;top:60px;width:60px">Short line about this service</div>
  <div class="p ctr" style="left:192px;top:60px;width:60px">Short line about this service</div>
  <div class="lbl ctr" style="left:6px;top:105px;width:60px">Título</div>
  <div class="lbl ctr" style="left:72px;top:105px;width:60px">Título</div>
  <div class="lbl ctr" style="left:135px;top:105px;width:60px">Título</div>
  <div class="lbl ctr" style="left:192px;top:105px;width:60px">Título</div>
  <div class="p ctr" style="left:6px;top:111px;width:60px">Short line about this service</div>
  <div class="p ctr" style="left:72px;top:111px;width:60px">Short line about this service</div>
  <div class="p ctr" style="left:135px;top:111px;width:60px">Short line about this service</div>
  <div class="p ctr" style="left:192px;top:111px;width:60px">Short line about this service</div>
  <div class="foot"><span>Human Resources services &amp; business coaching</span><span>CoachWorks 21</span></div>
</section>

<!-- 22 cycle -->
<section class="slide c2 r6">
  <div class="logo" style="left:18px;top:8px"><i></i>CoachWorks</div>
  <div class="title" style="left:82px;top:8px">Your title <b>slide here</b></div>
  <div class="lbl" style="left:19px;top:42px;font-weight:400">Título</div>
  <div class="p" style="left:19px;top:47px;width:48px;text-align:left">Short note on the first step here</div>
  <div class="lbl" style="left:19px;top:83px;font-weight:400">Título</div>
  <div class="p" style="left:19px;top:88px;width:48px;text-align:left">Short note on the third step here</div>
  <div class="lbl" style="left:200px;top:42px;font-weight:400;text-align:right;width:42px">Título</div>
  <div class="p" style="left:192px;top:47px;width:50px;text-align:right">Short note on the second step here</div>
  <div class="lbl" style="left:200px;top:83px;font-weight:400;text-align:right;width:42px">Título</div>
  <div class="p" style="left:192px;top:88px;width:50px;text-align:right">Short note on the fourth step here</div>
  <svg class="abs" style="left:75px;top:26px" width="110" height="100" viewBox="0 0 110 100">
    <circle cx="30" cy="24" r="13" fill="var(--purple)"/><circle cx="78" cy="24" r="13" fill="var(--orange)"/>
    <circle cx="32" cy="78" r="13" fill="var(--teal)"/><circle cx="80" cy="78" r="13" fill="var(--pink)"/>
    <g font-family="Roboto,sans-serif" font-size="7.5" font-weight="500" fill="#fff" text-anchor="middle">
      <text x="30" y="27">01</text><text x="78" y="27">02</text><text x="32" y="81">03</text><text x="80" y="81">04</text>
    </g>
    <g fill="none" stroke-width="2">
      <path d="M40 33 Q55 22 68 38" stroke="var(--purple)"/>
      <path d="M76 42 Q78 58 66 68" stroke="var(--orange)"/>
      <path d="M64 72 Q50 80 42 68" stroke="var(--pink)"/>
      <path d="M30 64 Q30 48 42 40" stroke="var(--teal)"/>
    </g>
  </svg>
  <div class="foot"><span>Human Resources services &amp; business coaching</span><span>CoachWorks 22</span></div>
</section>

<!-- 23 illustration area -->
<section class="slide c3 r6">
  <div class="logo" style="left:18px;top:8px"><i></i>CoachWorks</div>
  <div class="title" style="left:82px;top:8px">Your title <b>slide here</b></div>
  <div class="lbl" style="left:21px;top:40px">Título</div>
  <div class="p" style="left:21px;top:52px;width:108px;text-align:left;line-height:1.9">Strong teams start with clear thinking. We help owners see the whole business at once: people, process, money and sales. With that view in hand, decisions get faster, plans get simpler and everyone knows the part they play in reaching the goal. Each session ends with one clear action for the week ahead.</div>
  <div class="ph ph-line" style="left:150px;top:24px;width:110px;height:117px" role="img" aria-label="Line illustration of a head in profile with coloured points"></div>
  <div class="foot"><span>Human Resources services &amp; business coaching</span><span>CoachWorks 23</span></div>
</section>

<!-- 24 contact -->
<section class="slide c4 r6">
  <div class="logo" style="left:18px;top:12px"><i></i>CoachWorks</div>
  <div class="title" style="left:178px;top:11px;font-size:9.5px">Contact <b>us</b></div>
  <div class="ph ph-crowd" style="left:0;top:30px;width:260px;height:61px" role="img" aria-label="Crowd of commuters in a busy hall"></div>
  <svg class="abs" style="left:0;top:96px" width="260" height="30" viewBox="0 0 260 30">
    <g fill="none" stroke="#666" stroke-width=".8">
      <path d="M10 17 C4 10 5 5 10 5 C15 5 16 10 10 17 Z"/><circle cx="10" cy="9" r="1.8"/>
      <path d="M74 17 C68 10 69 5 74 5 C79 5 80 10 74 17 Z"/><circle cx="74" cy="9" r="1.8"/>
      <rect x="134" y="5" width="13" height="9"/><path d="M134 5 L140.5 10 L147 5"/>
      <rect x="204" y="3" width="8" height="13" rx="1.5"/><line x1="207" y1="14" x2="209" y2="14"/>
    </g>
  </svg>
  <div class="abs" style="left:21px;top:98px;font-size:3.6px;color:var(--purple);font-weight:500">Office A</div>
  <div class="p" style="left:21px;top:103px;width:45px;text-align:left">[]</div>
  <div class="abs" style="left:85px;top:98px;font-size:3.6px;color:var(--purple);font-weight:500">Office B</div>
  <div class="p" style="left:85px;top:103px;width:45px;text-align:left">[]</div>
  <div class="abs" style="left:153px;top:98px;font-size:3.6px;color:var(--purple);font-weight:500">EMAIL / WEBSITE</div>
  <div class="p" style="left:153px;top:103px;width:45px;text-align:left">[]</div>
  <div class="abs" style="left:220px;top:98px;font-size:3.6px;color:var(--purple);font-weight:500">Phones</div>
  <div class="p" style="left:220px;top:103px;width:35px;text-align:left">[]</div>
  <div class="foot plain"><span>Human Resources services &amp; business coaching</span><span>CoachWorks 24</span></div>
</section>

</div>
</body>
</html>
```